Quill Harbour Business Card

I need a business card designed around my logo (which was designed here on Art Meadow!)

Target Market(s)

Professional Businesses

Industry/Entity Type

Business

Requirements
Must have
• Details that must be on the business card:

Harriet Vonkamp
Director
0491 570 156
harriet@quillharbour.com.au
www.quillharbour.com.au
PO Box 4572 Brindle Park NW 2741

```html
<!DOCTYPE html>
<html lang="en">
<head>
<meta charset="utf-8">
<title>Quill Harbour Business Card</title>
<link href="https://fonts.googleapis.com/css2?family=Cinzel:wght@400&family=Open+Sans:wght@400;700&display=swap" rel="stylesheet">
<style>
  :root {
    --page: #e9e7e4;
    --card-red: #b0001f;
    --card-red-deep: #7e0016;
    --card-white: #f1f1f1;
    --ink-grey: #8a8a8a;
    --ink-dark: #4a4a4a;
    --accent-red: #b0001f;
    --text-white: #ffffff;
    --serif: "Cinzel", "Times New Roman", serif;
    --sans: "Open Sans", Arial, sans-serif;
  }
  * { box-sizing: border-box; margin: 0; padding: 0; }
  html, body { width: 1200px; height: 900px; overflow: hidden; }
  body {
    background: var(--page);
    display: flex;
    align-items: center;
    justify-content: center;
    gap: 40px;
    font-family: var(--sans);
  }
  .card {
    width: 540px;
    height: 309px;
    position: relative;
    box-shadow: 0 6px 18px rgba(0,0,0,0.18);
  }
  /* Front: red */
  .card-front {
    background: var(--card-red);
    color: var(--text-white);
    display: flex;
    flex-direction: column;
    align-items: flex-end;
    justify-content: center;
    padding: 0 36px;
    text-align: right;
  }
  .front-name {
    font-family: var(--serif);
    font-size: 30px;
    letter-spacing: 1px;
    line-height: 1;
    text-transform: uppercase;
  }
  .front-tagline {
    font-family: var(--serif);
    font-size: 13px;
    letter-spacing: 4.6px;
    color: var(--card-red-deep);
    text-transform: uppercase;
    margin-top: 4px;
  }
  .front-web {
    font-size: 14px;
    letter-spacing: 4px;
    margin-top: 34px;
  }
  /* Back: white */
  .card-back {
    background: var(--card-white);
    display: flex;
    align-items: center;
    padding: 0 34px;
    gap: 30px;
  }
  .brand-square {
    width: 78px;
    height: 78px;
    background: var(--accent-red);
    flex: none;
    margin-top: -40px;
  }
  .back-content { display: flex; flex-direction: column; }
  .back-name {
    font-family: var(--serif);
    font-size: 28px;
    letter-spacing: 1px;
    line-height: 1;
    color: var(--ink-grey);
    text-transform: uppercase;
  }
  .back-tagline {
    font-family: var(--serif);
    font-size: 13px;
    letter-spacing: 4.2px;
    color: var(--accent-red);
    text-transform: uppercase;
    margin-top: 3px;
  }
  .person { margin-top: 26px; color: var(--ink-dark); font-size: 14px; }
  .person-name { font-weight: 700; font-size: 17px; }
  .person-role { font-size: 12px; text-transform: uppercase; margin-left: 6px; }
  .contact { margin-top: 8px; font-size: 13.5px; line-height: 1.55; color: var(--ink-dark); }
  .contact-label { color: var(--accent-red); margin-right: 4px; }
  .contact-web { color: var(--accent-red); font-weight: 700; font-size: 14.5px; }
</style>
</head>
<body>
  <section class="card card-front">
    <p class="front-name">Quill Harbour</p>
    <p class="front-tagline">Accounts kept simple</p>
    <p class="front-web">www.quillharbour.com.au</p>
  </section>

  <section class="card card-back">
    <div class="brand-square" aria-hidden="true"></div>
    <div class="back-content">
      <p class="back-name">Quill Harbour</p>
      <p class="back-tagline">Accounts kept simple</p>
      <p class="person"><span class="person-name">Harriet Vonkamp</span><span class="person-role">Director</span></p>
      <div class="contact">
        <p><span class="contact-label">t</span>0491 570 156</p>
        <p><span class="contact-label">e</span>harriet@quillharbour.com.au</p>
        <p>PO Box 4572 Brindle Park NW 2741</p>
        <p class="contact-web">www.quillharbour.com.au</p>
      </div>
    </div>
  </section>
</body>
</html>
```